Single-sided business card for restaurant velmora with new logo made on this site

Business card options with new logo including restaurant name, address, phone number and website. This business card is single-sided only and will be presented at the hostess desk for clients to take. I would like to see options based on a cream card background, a white card background, a yellow card background and a burgundy colored background. It needs to be elegant and traditional.

Target Market(s)

local and international crowd

Industry/Entity Type

restaurant

Contact Information for Business Card

address, website and phone number

Font styles to use
Serif

Colors
EE7325
F08F49
F5BC92
FAE3D3
FDF4ED

Requirements
Must have
• new logo, address, phone number, website
Should not have
• more than three colors

```html
<!DOCTYPE html>
<html lang="es">
<head>
<meta charset="utf-8">
<title>Velmora – Tarjeta de presentación</title>
<link rel="stylesheet" href="https://fonts.googleapis.com/css2?family=Cinzel:wght@400;600&family=Cormorant+Garamond:wght@500&family=Noto+Sans:wght@400&display=swap">
<style>
  :root {
    --backdrop: #2b2b2b;
    --card: #ffffff;
    --gold: #f2b12a;
    --burgundy: #4a1a1a;
    --ink: #3c1a14;
    --haze: #f1ebe0;
  }
  html, body {
    margin: 0;
    width: 1200px;
    height: 866px;
    overflow: hidden;
    background: var(--backdrop);
  }
  .card {
    position: absolute;
    left: 100px;
    top: 147px;
    width: 1000px;
    height: 572px;
    background: var(--card);
    overflow: hidden;
    box-shadow: 0 12px 30px rgba(0,0,0,.45);
  }
  .leaf-pattern {
    position: absolute;
    left: 140px;
    top: 20px;
    width: 620px;
    height: 430px;
    background: radial-gradient(ellipse at 50% 60%, var(--haze) 0%, rgba(241,235,224,.5) 45%, rgba(255,255,255,0) 72%);
  }
  .reservations {
    position: absolute;
    left: 62px;
    top: 46px;
    margin: 0;
  }
  .reservations-label {
    display: block;
    font-family: "Cinzel", serif;
    font-size: 30px;
    font-weight: 400;
    color: var(--gold);
    letter-spacing: 1px;
  }
  .reservations-phone {
    display: block;
    font-family: "Cormorant Garamond", serif;
    font-size: 56px;
    font-weight: 500;
    color: var(--ink);
    letter-spacing: 2px;
    line-height: 1;
    margin-top: 2px;
  }
  .divider {
    position: absolute;
    left: 60px;
    top: 232px;
    width: 600px;
    height: 1px;
    background: var(--gold);
    opacity: .7;
  }
  .address {
    position: absolute;
    left: 62px;
    top: 262px;
    margin: 0;
    font-family: "Noto Sans", sans-serif;
    font-style: normal;
    font-size: 23px;
    line-height: 1.3;
    color: var(--ink);
  }
  .brand {
    position: absolute;
    left: 690px;
    top: 150px;
    width: 270px;
    text-align: center;
  }
  .brand-square {
    display: block;
    width: 190px;
    height: 170px;
    margin: 0 auto 18px;
    background: var(--gold);
  }
  .brand-name {
    margin: 0;
    font-family: "Cinzel", serif;
    font-size: 50px;
    font-weight: 600;
    letter-spacing: 6px;
    color: var(--ink);
  }
  .footer-band {
    position: absolute;
    left: 0;
    bottom: 0;
    width: 1000px;
    height: 90px;
  }
  .website {
    position: absolute;
    right: 70px;
    bottom: 18px;
    margin: 0;
    font-family: "Noto Sans", sans-serif;
    font-size: 27px;
    letter-spacing: 2px;
    color: var(--card);
  }
</style>
</head>
<body>
  <main class="card">
    <div class="leaf-pattern" role="img" aria-label="Faint agave leaf pattern in the card background"></div>

    <p class="reservations">
      <span class="reservations-label">Reservaciones</span>
      <span class="reservations-phone">958-214-3370</span>
    </p>

    <div class="divider"></div>

    <address class="address">
      Restaurant Velmora, Camelia 418<br>
      Bahías de Tolanco<br>
      Oaxaca CP 70934
    </address>

    <div class="brand">
      <span class="brand-square"></span>
      <p class="brand-name">VELMORA</p>
    </div>

    <svg class="footer-band" viewBox="0 0 1000 90" aria-hidden="true">
      <path d="M0 64 H420 C455 64 460 22 500 22 H1000 V90 H0 Z" fill="var(--burgundy)"/>
      <path d="M0 54 H420 C450 54 458 14 492 12 L500 22 C460 22 455 64 420 64 H0 Z" fill="var(--gold)"/>
    </svg>

    <p class="website">www.velmora.com.mx</p>
  </main>
</body>
</html>
```